Quiet Lanterns for the Restless Inner Mind

I would like a website designed that would be used to upload podcasts, videos and written material about mental health. Where people will be being as honest, open and truthful as they can about mental health issues.
I would like it to look calming and soothing. Inspired by Dorlac's paintings and colour schemes.

I am on Brightlane as Dr Helen Maddox - and chirpbox as drhelenmaddox

Target Market(s)

Healthcare professionals and users of services who want to think at a deeper level about the nature of mental illness

Number of Pages Required

1 page

```html
<!DOCTYPE html>
<html lang="en">
<head>
<meta charset="utf-8">
<title>Dr Helen Maddox — Quiet Lanterns for the Restless Inner Mind</title>
<link rel="stylesheet" href="https://fonts.googleapis.com/css2?family=Josefin+Sans:wght@400;600;700&family=Raleway:wght@300;400;500&display=swap">
<style>
:root{
  --slate:#4f6c73;
  --slate-dark:#46636a;
  --teal-heading:#4e6d74;
  --sage:#b3bca7;
  --sage-contact:#a7b39b;
  --ink:#0b0c0f;
  --white:#ffffff;
  --grey-line:#b9bdb5;
  --text:#2f3a3c;
  --mist:#e9ebe6;
  --accent-green:#2e8a5e;
}
*{margin:0;padding:0;box-sizing:border-box}
html,body{width:1200px;height:3657px;overflow:hidden}
body{position:relative;font-family:"Raleway",sans-serif;color:var(--text);background:var(--white)}
.abs{position:absolute}
.display{font-family:"Josefin Sans",sans-serif}
.btn{position:absolute;background:var(--slate);color:var(--white);font-family:"Josefin Sans",sans-serif;font-weight:600;font-size:13px;letter-spacing:.08em;text-transform:uppercase;display:flex;align-items:center;justify-content:center}
.rule{position:absolute;height:2px;background:var(--grey-line)}
.section-title{position:absolute;left:0;width:1200px;text-align:center;font-family:"Josefin Sans",sans-serif;font-weight:600;font-size:46px;letter-spacing:.03em;color:var(--teal-heading)}

/* hero */
.hero{position:absolute;left:0;top:0;width:1200px;height:636px;background:linear-gradient(180deg,#b9a893 0%,#c89b74 35%,#a46f4a 65%,#3d3229 100%)}
.hero-silhouette{position:absolute;left:180px;top:110px;width:460px;height:526px;background:radial-gradient(ellipse at 45% 30%,#f3c07a 0%,#6a4330 25%,#2a1f1b 60%);border-radius:45% 45% 0 0}
.brand{font-family:"Josefin Sans",sans-serif;font-weight:600;font-size:23px;color:var(--white);letter-spacing:.01em}
.nav{display:flex;gap:38px;font-family:"Josefin Sans",sans-serif;font-weight:600;font-size:14px;color:var(--white);letter-spacing:.04em}
.nav .active{border-bottom:2px solid var(--white);padding-bottom:4px}
.hero-title{left:660px;top:130px;width:440px;font-family:"Josefin Sans",sans-serif;font-weight:600;font-size:45px;line-height:44px;color:var(--white);letter-spacing:.02em}
.hero-copy{left:663px;top:327px;width:400px;font-family:"Josefin Sans",sans-serif;font-size:13.5px;line-height:17px;color:var(--white)}
.dots{left:574px;top:586px;display:flex;gap:11px}
.dots span{width:10px;height:10px;border-radius:50%;background:var(--white)}
.dots span:first-child{background:#c9ccc4}

/* roles band */
.roles{position:absolute;left:0;top:636px;width:1200px;height:205px;background:var(--sage)}
.role{position:absolute;top:0;height:205px;color:#2b3436;font-size:14.5px;line-height:21px}
.role svg{position:absolute;top:34px}
.role p{position:absolute;top:128px;white-space:nowrap}
.divider{position:absolute;top:0;width:1px;height:205px;background:#c9d0bf}

/* about */
.about{position:absolute;left:0;top:841px;width:1200px;height:468px;background:var(--ink)}
.about-photo{position:absolute;left:0;top:0;width:483px;height:468px;background:radial-gradient(ellipse at 40% 45%,#c89a80 0%,#7a4a36 40%,#1b1413 80%)}
.about h2{left:604px;top:72px;font-family:"Josefin Sans",sans-serif;font-weight:600;font-size:46px;color:var(--white);letter-spacing:.02em}
.about-copy{left:604px;top:167px;width:465px;font-size:14px;line-height:21.6px;color:#e2e4e0;font-weight:300}

/* podcasts */
.pod-card{position:absolute;top:1460px;width:223px}
.pod-img{width:223px;height:236px;position:relative}
.pod-time{position:absolute;left:6px;top:18px;background:rgba(255,255,255,.55);color:var(--white);font-size:11px;padding:3px 6px;font-family:"Josefin Sans",sans-serif}
.pod-cap{display:flex;gap:12px;margin-top:15px;align-items:flex-start}
.pod-cap p{font-family:"Josefin Sans",sans-serif;font-weight:600;font-size:12.5px;line-height:17px;color:#1f2628;letter-spacing:.02em}

/* videos */
.videos{position:absolute;left:0;top:1872px;width:1200px;height:528px;background:linear-gradient(180deg,#eceeea 0%,#e6e5df 60%,#d9dad2 100%)}
.video{position:absolute;top:136px;width:462px;height:291px}
.play{position:absolute;left:50%;top:50%;transform:translate(-50%,-50%)}

/* written */
.written-img{position:absolute;left:456px;top:2438px;width:724px;height:482px;background:linear-gradient(135deg,#8c7a68 0%,#6f7683 40%,#3f5a82 70%,#262c34 100%)}
.written-title span{display:inline-block;background:var(--white);padding:0 14px 0 0;font-family:"Josefin Sans",sans-serif;font-weight:600;font-size:46px;line-height:53px;color:var(--teal-heading);letter-spacing:.03em}
.written-copy{left:135px;top:2691px;width:295px;font-size:14px;line-height:21.6px;color:#3a4345;font-weight:400}

/* contact */
.contact{position:absolute;left:0;top:2965px;width:1200px;height:511px;background:linear-gradient(160deg,#a9b59d 0%,#b2bca6 50%,#a5b199 100%)}
.field{position:absolute;background:var(--white);font-size:13px;color:#7d8583;padding:18px 20px}

/* footer */
.footer{position:absolute;left:0;top:3476px;width:1200px;height:181px;background:var(--slate-dark)}
.social{display:flex;align-items:center;gap:18px;font-family:"Josefin Sans",sans-serif;color:var(--white)}
</style>
</head>
<body>

<header class="hero">
  <div class="hero-silhouette" role="img" aria-label="Silhouette of a woman in a hat at sunset over a field"></div>
  <div class="abs brand" style="left:132px;top:30px">Dr Helen Maddox</div>
  <nav class="abs nav" style="left:561px;top:36px">
    <span class="active">HOME</span><span>ABOUT ME</span><span>PODCASTS</span><span>VIDEOS</span><span>CONTACT ME</span>
  </nav>
  <h1 class="abs hero-title">HEALING MINDS, CHANGING LIVES: MENTAL HEALTH AWARENESS</h1>
  <p class="abs hero-copy">Lorem ipsum dolor sit amet, consectetur adipiscing elit, sed do eiusmod tempor incididunt ut labore et dolore magna aliqua. Ut enim ad minim veniam</p>
  <div class="btn" style="left:665px;top:404px;width:120px;height:36px">Read More</div>
  <div class="abs dots"><span></span><span></span><span></span></div>
</header>

<section class="roles">
  <div class="role" style="left:133px">
    <svg width="72" height="72" viewBox="0 0 72 72" style="left:0"><circle cx="36" cy="36" r="34" fill="none" stroke="#fff" stroke-width="2"/><g fill="#fff"><circle cx="27" cy="26" r="4"/><circle cx="45" cy="26" r="4"/><circle cx="36" cy="30" r="4"/><rect x="22" y="32" width="10" height="14" rx="3"/><rect x="40" y="32" width="10" height="14" rx="3"/><rect x="31" y="36" width="10" height="14" rx="3"/></g></svg>
    <p>Chair Working Group on the Effect of<br>Suicide and Homicide on Clinicians</p>
  </div>
  <div class="divider" style="left:418px"></div>
  <div class="role" style="left:439px">
    <svg width="72" height="72" viewBox="0 0 72 72" style="left:0"><circle cx="36" cy="36" r="34" fill="none" stroke="#fff" stroke-width="2"/><path d="M36 20l10 4v8c0 6-4 10-10 12-6-2-10-6-10-12v-8z" fill="#fff"/><path d="M20 40c4 4 8 10 16 12 8-2 12-8 16-12" fill="none" stroke="#fff" stroke-width="3"/></svg>
    <p>Co-Chair Patient<br>Safety Group</p>
  </div>
  <div class="divider" style="left:582px"></div>
  <div class="role" style="left:612px">
    <svg width="72" height="72" viewBox="0 0 72 72" style="left:7px"><circle cx="36" cy="36" r="34" fill="none" stroke="#fff" stroke-width="2"/><path d="M24 50V36c0-9 6-16 14-16s12 6 12 13l4 7h-4v6h-8v4z" fill="#fff"/><circle cx="38" cy="33" r="6" fill="none" stroke="#b3bca7" stroke-width="2"/></svg>
    <p>Vice Chair<br>Psychotherapy Faculty</p>
  </div>
  <div class="divider" style="left:804px"></div>
  <div class="role" style="left:834px">
    <svg width="72" height="72" viewBox="0 0 72 72" style="left:3px"><circle cx="36" cy="36" r="34" fill="none" stroke="#fff" stroke-width="2"/><circle cx="36" cy="30" r="8" fill="#fff"/><path d="M22 52c0-9 6-13 14-13s14 4 14 13z" fill="#fff"/></svg>
    <p>Psychoanalyst</p>
  </div>
  <div class="divider" style="left:961px"></div>
  <div class="role" style="left:986px">
    <svg width="72" height="72" viewBox="0 0 72 72" style="left:5px"><circle cx="36" cy="36" r="34" fill="none" stroke="#fff" stroke-width="2"/><g fill="#fff"><circle cx="26" cy="30" r="5"/><circle cx="46" cy="30" r="5"/><circle cx="36" cy="28" r="6"/><path d="M16 46c0-6 4-9 10-9s10 3 10 9z"/><path d="M36 46c0-6 4-9 10-9s10 3 10 9z"/><path d="M25 46c0-7 5-10 11-10s11 3 11 10z"/></g></svg>
    <p>Group<br>Analyst</p>
  </div>
</section>

<section class="about">
  <div class="about-photo" role="img" aria-label="Portrait of Dr Helen Maddox"></div>
  <h2 class="abs">ABOUT ME</h2>
  <div class="abs" style="left:604px;top:133px;width:50px;height:2px;background:var(--accent-green)"></div>
  <p class="abs about-copy">Sed ut perspiciatis unde omnis iste natus error sit voluptatem accusantium doloremque laudantium, totam rem aperiam, eaque ipsa quae ab illo inventore veritatis et quasi architecto beatae vitae dicta sunt explicabo. Nemo enim ipsam voluptatem quia voluptas sit aspernatur aut odit aut fugit, sed quia consequuntur magni dolores eos qui ratione voluptatem sequi nesciunt. Neque porro quisquam est, qui dolorem ipsum quia dolor sit ame</p>
  <div class="btn" style="left:605px;top:347px;width:121px;height:34px">Read More</div>
</section>

<section>
  <h2 class="section-title" style="top:1352px">PODCASTS</h2>
  <div class="rule" style="left:574px;top:1417px;width:52px"></div>

  <article class="pod-card" style="left:133px">
    <div class="pod-img" role="img" aria-label="Person sitting by a mountain lake" style="background:linear-gradient(180deg,#8fa08a 0%,#4f6b55 45%,#2c3a33 100%)"><span class="pod-time">04:59</span></div>
    <div class="pod-cap"><svg width="32" height="32" viewBox="0 0 32 32"><circle cx="16" cy="16" r="16" fill="#6a9fd4"/><path d="M12 9l11 7-11 7z" fill="#fff"/></svg><p>LOREM IPSUM DOLOR SIT<br>AMET CONSECTETUR ADI</p></div>
  </article>
  <article class="pod-card" style="left:372px">
    <div class="pod-img" role="img" aria-label="Hand holding a wooden block with a smile" style="background:linear-gradient(135deg,#f2ece6 0%,#e7d2c2 55%,#d9b89c 100%)"><span class="pod-time">04:59</span></div>
    <div class="pod-cap"><svg width="32" height="32" viewBox="0 0 32 32"><circle cx="16" cy="16" r="16" fill="#6a9fd4"/><path d="M12 9l11 7-11 7z" fill="#fff"/></svg><p>LOREM IPSUM DOLOR SIT<br>AMET CONSECTETUR ADI</p></div>
  </article>
  <article class="pod-card" style="left:609px">
    <div class="pod-img" role="img" aria-label="Figure in a sunlit meadow with birds" style="background:linear-gradient(180deg,#aebfc6 0%,#e9d6a6 45%,#c8a56b 100%)"><span class="pod-time">04:59</span></div>
    <div class="pod-cap"><svg width="32" height="32" viewBox="0 0 32 32"><circle cx="16" cy="16" r="16" fill="#6a9fd4"/><path d="M12 9l11 7-11 7z" fill="#fff"/></svg><p>LOREM IPSUM DOLOR SIT<br>AMET CONSECTETUR ADI</p></div>
  </article>
  <article class="pod-card" style="left:846px">
    <div class="pod-img" role="img" aria-label="Hands holding a yellow smiling ball" style="background:radial-gradient(circle at 50% 55%,#f4c531 0%,#e0b030 22%,#4fa0a4 48%,#3b8c93 100%)"><span class="pod-time">04:59</span></div>
    <div class="pod-cap"><svg width="32" height="32" viewBox="0 0 32 32"><circle cx="16" cy="16" r="16" fill="#6a9fd4"/><path d="M12 9l11 7-11 7z" fill="#fff"/></svg><p>LOREM IPSUM DOLOR SIT<br>AMET CONSECTETUR ADI</p></div>
  </article>

  <div class="btn" style="left:514px;top:1786px;width:172px;height:34px">View All Podcasts</div>
</section>

<section class="videos">
  <h2 class="section-title" style="top:34px">VIDEOS</h2>
  <div class="rule" style="left:574px;top:99px;width:52px"></div>
  <div class="video" role="img" aria-label="Video still of a man in distress on a sofa" style="left:132px;background:linear-gradient(120deg,#9aa3a3 0%,#c9c6bd 45%,#ecebe6 100%)">
    <svg class="play" width="36" height="36" viewBox="0 0 32 32"><circle cx="16" cy="16" r="16" fill="#6a9fd4"/><path d="M12 9l11 7-11 7z" fill="#fff"/></svg>
  </div>
  <div class="video" role="img" aria-label="Video still of a group therapy session" style="left:606px;background:linear-gradient(120deg,#8d9389 0%,#5e5f5a 45%,#2d3236 100%)">
    <svg class="play" width="36" height="36" viewBox="0 0 32 32"><circle cx="16" cy="16" r="16" fill="#6a9fd4"/><path d="M12 9l11 7-11 7z" fill="#fff"/></svg>
  </div>
  <div class="btn" style="left:524px;top:457px;width:151px;height:34px">View All Videos</div>
</section>

<section>
  <div class="written-img" role="img" aria-label="Therapist taking notes during a session"></div>
  <h2 class="abs written-title" style="left:132px;top:2482px;width:480px">
    <span>WRITTEN MATERIAL</span><br><span>ABOUT MENTAL</span><br><span>HEALTH</span>
  </h2>
  <div class="rule" style="left:135px;top:2660px;width:52px"></div>
  <p class="abs written-copy">Sed ut perspiciatis unde omnis iste natus error sit voluptatem accusantium dolor emque laudantium, totam rem aperiam, eaque ipsa quae ab illo inventore veritatis et quasi architecto beatae vitae dicta sunt explicabo. Nemo enim ipsam voluptatem quia voluptas sit aspernatu.</p>
  <div class="btn" style="left:138px;top:2867px;width:112px;height:36px">Read More</div>
</section>

<section class="contact">
  <h2 class="section-title" style="top:48px;color:var(--white)">CONTACT ME</h2>
  <div class="rule" style="left:574px;top:111px;width:52px;background:var(--white)"></div>
  <div class="field" style="left:267px;top:155px;width:327px;height:48px">First Name</div>
  <div class="field" style="left:605px;top:155px;width:326px;height:48px">Last Name</div>
  <div class="field" style="left:267px;top:215px;width:327px;height:48px">Email id</div>
  <div class="field" style="left:605px;top:215px;width:326px;height:48px">Phone</div>
  <div class="field" style="left:267px;top:274px;width:667px;height:127px">Message</div>
  <div class="btn" style="left:561px;top:433px;width:78px;height:34px">Submit</div>
</section>

<footer class="footer">
  <div class="abs brand" style="left:133px;top:40px">Dr Helen Maddox</div>
  <nav class="abs nav" style="left:562px;top:46px;gap:37px"><span>HOME</span><span>ABOUT ME</span><span>PODCASTS</span><span>VIDEOS</span><span>CONTACT ME</span></nav>
  <div class="abs" style="left:133px;top:98px;width:936px;height:1px;background:#6d878b"></div>
  <div class="abs social" style="left:134px;top:130px">
    <span style="font-size:11px;font-weight:600;letter-spacing:.05em">FOLLOW US</span>
    <span style="font-size:13px;font-weight:600">Brightlane</span>
    <span style="font-size:13px;font-weight:600">chirpbox</span>
  </div>
  <div class="abs" style="left:830px;top:134px;width:242px;text-align:right;font-size:10.5px;color:var(--white)">Copyright © 2023 All Rights Reserved</div>
</footer>

</body>
</html>
```